Banner Design 4040mm W x 2190mm H

Design a glamorous and exciting 4040mm W x 2190mm H backdrop for the QLMRT Velvet Harbour Gala at the luxurious Tamsin Hall, Vellora, Whitcombe Quay, Sydney. This exciting backdrop should be spectacular so that people will be excited to take photos in front of it.
Design Colours preferred is black and pink.
Please include our website on the banner www.qlmrt.org.au
Should include the words "QLMRT Velvet Harbour Gala" as the main attraction on the banner.
Please include "Thank you to our sponsors" and include the logo of the sponsors.
Sponsors:
Brenwick Pathology
NorthGlen Radiology
KTV Diagnostic Imaging
Harbin Legal Partners
Denhams
Banner Template:
4040mm W x 2190mm H Single Sided (.AI)
https://files.examplestore.net/d/8Rk2mZpQ7vLx3TnW5yBc/view
QLMRT Logo:
Can be obtained from our website www.qlmrt.org.au

```html
<!DOCTYPE html>
<html lang="en">
<head>
<meta charset="utf-8">
<title>QLMRT Velvet Harbour Gala – Sponsor Backdrop</title>
<link rel="stylesheet" href="https://fonts.googleapis.com/css2?family=Montserrat:wght@500;600;700&family=Yellowtail&family=Satisfy&display=block">
<style>
  :root {
    --page-bg: #d4d4d4;
    --backdrop-black: #000000;
    --glow-pink: #e23fd2;
    --glow-deep: #6a1550;
    --glow-amber: #3a2314;
    --headline-yellow: #f7f21a;
    --script-pink: #e44ad8;
    --text-white: #ffffff;
    --strip-white: #ffffff;
    --strip-divider: #c9c9c9;
    --sponsor-ink: #1f2a5a;
  }
  * { box-sizing: border-box; margin: 0; padding: 0; }
  html, body { width: 1121px; height: 1200px; overflow: hidden; }
  body { background: var(--page-bg); position: relative; font-family: "Montserrat", sans-serif; }

  .backdrop {
    position: absolute; left: 40px; top: 318px;
    width: 1040px; height: 564px;
    background: var(--backdrop-black);
    overflow: hidden;
  }
  .backdrop__glow {
    position: absolute; inset: 0;
    background:
      radial-gradient(ellipse 200px 150px at 50% 0%, rgba(255,190,255,0.85), rgba(255,120,240,0) 100%),
      radial-gradient(circle 46px at 30% 30%, rgba(170,60,150,0.35), rgba(0,0,0,0) 100%),
      radial-gradient(circle 52px at 66% 24%, rgba(190,70,170,0.35), rgba(0,0,0,0) 100%),
      radial-gradient(circle 48px at 85% 38%, rgba(120,70,40,0.45), rgba(0,0,0,0) 100%),
      radial-gradient(circle 44px at 6% 30%, rgba(110,60,35,0.45), rgba(0,0,0,0) 100%),
      radial-gradient(ellipse 520px 280px at 52% 0%, var(--glow-pink), rgba(160,40,150,0.55) 45%, rgba(0,0,0,0) 100%),
      radial-gradient(ellipse 700px 330px at 50% 0%, var(--glow-deep), rgba(0,0,0,0) 100%),
      radial-gradient(ellipse 260px 220px at 5% 20%, var(--glow-amber), rgba(0,0,0,0) 100%),
      radial-gradient(ellipse 260px 220px at 96% 25%, var(--glow-amber), rgba(0,0,0,0) 100%);
  }

  .org-mark {
    position: absolute; left: 46px; top: 64px;
    display: flex; align-items: center; gap: 8px;
    color: var(--text-white); font-weight: 700; font-size: 22px; letter-spacing: 1px;
  }
  .org-mark__dot { width: 16px; height: 16px; border-radius: 50%; background: var(--headline-yellow); }

  .script { font-family: "Yellowtail", "Satisfy", "Brush Script MT", cursive; font-weight: 400; }

  .headline {
    position: absolute; left: 183px; top: 92px;
    font-size: 168px; line-height: 1;
    color: var(--headline-yellow);
    white-space: nowrap;
  }
  .subhead {
    position: absolute; left: 274px; top: 266px;
    font-size: 38px; font-weight: 500; color: var(--text-white);
    white-space: nowrap;
  }

  .sponsor-strip {
    position: absolute; left: 277px; top: 346px;
    width: 485px; height: 48px;
    background: var(--strip-white); border-radius: 5px;
    display: flex; align-items: center; padding: 0 6px;
    list-style: none;
  }
  .sponsor-strip__item {
    flex: 1; height: 34px;
    display: flex; align-items: center; justify-content: center; text-align: center;
    font-size: 8.5px; font-weight: 700; line-height: 1.15; color: var(--sponsor-ink);
    padding: 0 4px;
  }
  .sponsor-strip__item + .sponsor-strip__item { border-left: 1px solid var(--strip-divider); }

  .event-title {
    position: absolute; left: 237px; top: 418px;
    display: flex; align-items: baseline; gap: 22px; white-space: nowrap;
    font-weight: 400;
  }
  .event-title__org { font-size: 29px; font-weight: 500; color: var(--text-white); }
  .event-title__name { font-size: 62px; color: var(--script-pink); }

  .website {
    position: absolute; left: 0; right: 0; top: 522px;
    text-align: center; font-size: 15px; font-weight: 500; letter-spacing: 1px;
    color: var(--text-white);
  }
</style>
</head>
<body>
  <section class="backdrop">
    <div class="backdrop__glow" role="img" aria-label="Pink light burst with sparkles and soft bokeh circles fading into black"></div>

    <div class="org-mark"><span class="org-mark__dot"></span>QLMRT</div>

    <h1 class="headline script">Thank you</h1>
    <p class="subhead">to our sponsors</p>

    <ul class="sponsor-strip">
      <li class="sponsor-strip__item">Brenwick Pathology</li>
      <li class="sponsor-strip__item">KTV Diagnostic Imaging</li>
      <li class="sponsor-strip__item">Denhams</li>
      <li class="sponsor-strip__item">NorthGlen Radiology</li>
      <li class="sponsor-strip__item">Harbin Legal Partners</li>
    </ul>

    <h2 class="event-title">
      <span class="event-title__org">QLMRT</span>
      <span class="event-title__name script">Velvet Harbour Gala</span>
    </h2>

    <p class="website">www.qlmrt.org.au</p>
  </section>
</body>
</html>
```